Creative Web design for Tattoo Artist

I am a tattoo artist with a private tattoo/art studio in Spring, TX. I need to design a website for my studio, to include the following "pages" :
-home/about
-FAQ
-Gallery
-Inquiries
-shop
We would like to see designs that are more dark or "moody", and like the colors black/gold.
I'd like my website to reflect my studio, an award winning private, upscale custom only tattoo studio.

I've attached some examples of styles we liked.

Target Market(s)

adults ages 18-50, interested in tattoos, or fine art

Industry/Entity Type

Tattoos/Fine Art/Arts

Coding

Coded - Design and coding required

Number of Pages Required

5+ page

Colors

Designer to choose colors to be used in the design.

Requirements
Must have
• gallery section, and e-commerce page set up so I can begin selling merchandise, I'd like the fonts to flow with my logo design

```html
<!DOCTYPE html>
<html lang="en">
<head>
<meta charset="utf-8">
<title>Gilded Raven — Private Tattoo Art Studio</title>
<link rel="stylesheet" href="https://fonts.googleapis.com/css2?family=Bitter:wght@400;500;700&family=IBM+Plex+Sans:wght@400;600&display=swap">
<style>
:root{
  --black:#000;
  --gold:#a8801e;
  --gold-bright:#c9a02a;
  --white:#fff;
  --text:#e6e6e6;
  --line:#3a3a3a;
  --photo-dark:#1c1c1c;
  --photo-mid:#6a6a6a;
  --photo-light:#b4b4b4;
}
*{margin:0;padding:0;box-sizing:border-box}
html,body{width:1200px;height:3873px;overflow:hidden;background:var(--black)}
body{position:relative;font-family:"Bitter",Georgia,serif;color:var(--text)}
.abs{position:absolute}

/* hero */
.hero-photo{left:0;top:0;width:1200px;height:690px;
  background:radial-gradient(ellipse at 60% 45%,#8a8a8a 0%,#4b4b4b 40%,#1e1e1e 80%)}
.hero-curve{left:0;top:560px;width:1200px;height:140px}
.brand{display:flex;align-items:center;gap:10px;font-family:"Bitter",serif;font-weight:500;font-size:20px;color:var(--white);letter-spacing:1px}
.brand-dot{width:14px;height:14px;border-radius:50%;background:var(--white)}
.site-brand{left:132px;top:110px}
.nav{top:31px;left:693px;display:flex;font-size:16px;color:var(--white)}
.nav a{position:absolute;white-space:nowrap;color:inherit;text-decoration:none}
.nav .active{color:var(--gold-bright)}
.nav .active::after{content:"";position:absolute;left:0;right:0;top:26px;height:2px;background:var(--gold-bright)}
.cart{left:1030px;top:26px}
.hero-title{left:131px;top:282px;font-size:50px;line-height:49px;font-weight:400;color:var(--white)}
.btn{display:inline-flex;align-items:center;justify-content:center;gap:10px;background:var(--gold);color:var(--white);
  border-radius:20px;font-size:15px;font-family:"Bitter",serif;white-space:nowrap}
.btn svg{width:8px;height:13px}
.dots{left:567px;top:626px;display:flex;gap:6px}
.dots span{width:12px;height:12px;border-radius:50%;border:1.5px solid var(--white)}
.dots .on{background:var(--gold);border-color:var(--gold)}

/* sections */
.heading{font-size:30px;color:var(--gold);font-weight:400;white-space:nowrap}
.rule{height:5px;border:1.5px solid #6b6b6b;border-radius:3px}
.rule.gold{border-color:var(--gold)}
.copy{font-size:13.5px;line-height:20.8px;color:var(--text);width:434px}
.pill-photo{border-radius:174px/200px}
.pill-outline{border:1.5px solid var(--gold);border-radius:174px/200px}
.photo-a{background:linear-gradient(160deg,#d0d0d0,#7a7a7a 55%,#2a2a2a)}
.photo-b{background:linear-gradient(200deg,#6e6e6e,#2c2c2c 60%,#111)}

.gallery{left:134px;top:1471px;display:grid;grid-template-columns:repeat(4,222px);grid-template-rows:329px 329px;column-gap:15px;row-gap:23px}
.gallery div{border-radius:111px/120px}
.g1{background:linear-gradient(180deg,#3a3a3a,#8a8a8a 50%,#222)}
.g2{background:linear-gradient(180deg,#2e3a44,#9a5a3a 55%,#6a3a28)}
.g3{background:linear-gradient(160deg,#cfcfcf,#6a6a6a 60%,#d8d8d8)}
.g4{background:linear-gradient(200deg,#9a9a9a,#4a4a4a 50%,#cfcfcf)}
.g5{background:linear-gradient(180deg,#2a2a2a,#5a5a5a 50%,#2c2c2c)}
.g6{background:linear-gradient(180deg,#e0e0e0,#9a9a9a 50%,#cccccc)}
.g7{background:linear-gradient(180deg,#3a3a3a,#8c8c8c 50%,#444)}
.g8{background:linear-gradient(180deg,#2a2a2a,#5c5c5c 50%,#1a1a1a)}

/* shop */
.card{width:222px;height:359px;border:1.5px solid var(--line);border-radius:4px;text-align:center}
.product{position:absolute;left:50%;transform:translateX(-50%);top:31px}
.card-title{position:absolute;left:0;right:0;top:171px;font-size:14px;font-weight:700;color:var(--white)}
.card-desc{position:absolute;left:14px;right:14px;top:203px;font-size:11.5px;line-height:17px;color:#d0d0d0}
.card-price{position:absolute;left:0;right:0;top:252px;font-size:18px;font-family:"IBM Plex Sans",sans-serif;color:var(--white)}
.card .btn{position:absolute;left:63px;top:295px;width:95px;height:25px;font-size:13px}

/* footer */
.footer{left:0;top:3513px;width:1200px;height:360px;background:linear-gradient(110deg,#141414,#1f1f1f 50%,#101010);font-family:"IBM Plex Sans",sans-serif}
.footer .label{position:absolute;font-size:13px;font-weight:600;color:var(--gold-bright);letter-spacing:.5px}
.footer .txt{position:absolute;font-size:11.5px;line-height:16px;color:var(--white)}
.footer .menu{font-size:11.5px}
.ico{position:absolute;width:23px;height:23px;border-radius:50%;background:var(--gold);display:flex;align-items:center;justify-content:center}
.ico svg{width:11px;height:11px}
.footer-brand{left:132px;top:147px}
.footer-rule{position:absolute;left:132px;top:262px;width:935px;height:1px;background:#333}
.copyright{position:absolute;left:0;right:0;top:301px;text-align:center;font-size:11px;color:var(--white)}
</style>
</head>
<body>

<!-- Hero -->
<div class="abs hero-photo" role="img" aria-label="Black and white photo of a tattoo artist inking a floral mandala on a forearm"></div>
<svg class="abs hero-curve" viewBox="0 0 1200 140" preserveAspectRatio="none" aria-hidden="true">
  <path d="M0 18 Q600 210 1200 18 L1200 140 L0 140 Z" fill="#000"/>
</svg>

<div class="abs brand site-brand"><span class="brand-dot"></span>Gilded Raven</div>

<nav class="abs nav">
  <a class="active" style="left:0">Home</a>
  <a style="left:81px">Gallery</a>
  <a style="left:176px">Inquiries</a>
  <a style="left:283px">Shop</a>
</nav>
<svg class="abs cart" width="36" height="30" viewBox="0 0 36 30" aria-label="Cart">
  <path d="M2 5h5l4 14h15l3-10H9" fill="none" stroke="#fff" stroke-width="2"/>
  <circle cx="13" cy="24" r="2" fill="#fff"/><circle cx="24" cy="24" r="2" fill="#fff"/>
  <circle cx="28" cy="6" r="6" fill="#a8801e"/>
  <text x="28" y="9" font-size="8" fill="#fff" text-anchor="middle" font-family="IBM Plex Sans,sans-serif">0</text>
</svg>

<h1 class="abs hero-title">Private Tattoo<br>Art Studio in<br>Spring</h1>
<a class="abs btn" style="left:132px;top:466px;width:124px;height:33px">Read more <svg viewBox="0 0 8 13"><path d="M1 1l5.5 5.5L1 12" fill="none" stroke="#fff" stroke-width="1.6"/></svg></a>

<div class="abs dots"><span></span><span class="on"></span><span></span><span></span></div>

<!-- Welcome -->
<h2 class="abs heading" style="left:143px;top:788px">Welcome to our studio</h2>
<div class="abs rule" style="left:146px;top:850px;width:119px"></div>
<p class="abs copy" style="left:146px;top:908px">Sed ut perspiciatis unde omnis iste natus error sit voluptatem accusantium doloremque laudantium, totam rem aperiam, eaque ipsa quae ab illo inventore veritatis et quasi architecto beatae vitae dicta sunt explicabo. Nemo enim ipsam voluptatem quia voluptas sit aspernatur aut odit aut fugit, sed quia consequuntur magni dolores eos qui ratione voluptatem sequi nesciunt. Neque porro quisquam est, qui dolorem ipsum quia dolor sit amet, consectetur, adipisci velit, sed quia non numquam eius modi tempora incidunt ut labore et dolore magnam aliquam quaerat voluptatem. Ut enim ad minima veniam, quis nostrum exercitationem ullam corporis suscipit laboriosam, nisi ut aliquid ex ea commodi consequatu</p>
<a class="abs btn" style="left:144px;top:1176px;width:122px;height:33px">Read more <svg viewBox="0 0 8 13"><path d="M1 1l5.5 5.5L1 12" fill="none" stroke="#fff" stroke-width="1.6"/></svg></a>

<div class="abs pill-outline" style="left:671px;top:755px;width:348px;height:512px"></div>
<div class="abs pill-photo photo-a" style="left:687px;top:741px;width:348px;height:512px" role="img" aria-label="Close-up of a gloved hand tattooing a geometric design on an arm"></div>

<!-- Gallery -->
<h2 class="abs heading" style="left:509px;top:1332px">Photo Gallery</h2>
<div class="abs rule gold" style="left:579px;top:1399px;width:42px"></div>
<div class="abs gallery">
  <div class="g1" role="img" aria-label="Tattooed man with folded arms in a corridor"></div>
  <div class="g2" role="img" aria-label="Back view of a heavily tattooed upper back and hands"></div>
  <div class="g3" role="img" aria-label="Tattoo machine working on a forearm"></div>
  <div class="g4" role="img" aria-label="Tattooed arm resting on sketches"></div>
  <div class="g5" role="img" aria-label="Bearded man showing tattooed forearms"></div>
  <div class="g6" role="img" aria-label="Woman with a mandala tattoo on her shoulder"></div>
  <div class="g7" role="img" aria-label="Young man resting on a tattooed arm"></div>
  <div class="g8" role="img" aria-label="Matching ornamental tattoos on both shins"></div>
</div>
<a class="abs btn" style="left:511px;top:2208px;width:161px;height:42px">View All Images <svg viewBox="0 0 8 13"><path d="M1 1l5.5 5.5L1 12" fill="none" stroke="#fff" stroke-width="1.6"/></svg></a>

<!-- Custom studio -->
<div class="abs pill-outline" style="left:151px;top:2353px;width:348px;height:512px"></div>
<div class="abs pill-photo photo-b" style="left:167px;top:2339px;width:348px;height:512px" role="img" aria-label="Gloved hands holding a tattoo machine over linework"></div>
<h2 class="abs heading" style="left:598px;top:2377px">Custom- Tattoo Studio</h2>
<div class="abs rule" style="left:600px;top:2443px;width:119px"></div>
<p class="abs copy" style="left:600px;top:2501px">Sed ut perspiciatis unde omnis iste natus error sit voluptatem accusantium doloremque laudantium, totam rem aperiam, eaque ipsa quae ab illo inventore veritatis et quasi architecto beatae vitae dicta sunt explicabo. Nemo enim ipsam voluptatem quia voluptas sit aspernatur aut odit aut fugit, sed quia consequuntur magni dolores eos qui ratione voluptatem sequi nesciunt. Neque porro quisquam est, qui dolorem ipsum quia dolor sit amet, consectetur, adipisci velit, sed quia non numquam eius modi tempora incidunt ut labore et dolore magnam aliquam quaerat voluptatem. Ut enim ad minima veniam, quis nostrum exercitationem ullam corporis suscipit laboriosam, nisi ut aliquid ex ea commodi consequatu</p>
<a class="abs btn" style="left:599px;top:2768px;width:123px;height:33px">Read more <svg viewBox="0 0 8 13"><path d="M1 1l5.5 5.5L1 12" fill="none" stroke="#fff" stroke-width="1.6"/></svg></a>

<!-- Shop -->
<h2 class="abs heading" style="left:565px;top:2939px">Shop</h2>
<div class="abs rule" style="left:579px;top:3007px;width:42px"></div>

<div class="abs card" style="left:132px;top:3067px">
  <div class="product" role="img" aria-label="Red baseball cap" style="width:140px;height:80px;border-radius:70px 70px 20px 20px;background:linear-gradient(160deg,#e0404a,#a81c28)"></div>
  <div class="card-title">Lorm Ipusm</div>
  <div class="card-desc">Sed ut perspiciatis unde omnis iste natus error sit voluptatem</div>
  <div class="card-price">$25.99</div>
  <a class="btn">Shop Now</a>
</div>
<div class="abs card" style="left:371px;top:3067px">
  <div class="product" role="img" aria-label="Yellow t-shirt" style="width:110px;height:110px;border-radius:10px;background:linear-gradient(160deg,#f4e05a,#d9bd2a)"></div>
  <div class="card-title">Lorm Ipusm</div>
  <div class="card-desc">Sed ut perspiciatis unde omnis iste natus error sit voluptatem</div>
  <div class="card-price">$25.99</div>
  <a class="btn">Shop Now</a>
</div>
<div class="abs card" style="left:608px;top:3067px">
  <div class="product" role="img" aria-label="Red coffee mug" style="width:100px;height:100px;border-radius:8px 8px 30px 30px;background:linear-gradient(120deg,#e22a2a,#8e0c0c)"></div>
  <div class="card-title">Lorm Ipusm</div>
  <div class="card-desc">Sed ut perspiciatis unde omnis iste natus error sit voluptatem</div>
  <div class="card-price">$25.99</div>
  <a class="btn">Shop Now</a>
</div>
<div class="abs card" style="left:844px;top:3067px">
  <div class="product" role="img" aria-label="Blue t-shirt" style="width:120px;height:105px;border-radius:10px;background:linear-gradient(160deg,#3bb8e6,#1a8cc0)"></div>
  <div class="card-title">Lorm Ipusm</div>
  <div class="card-desc">Sed ut perspiciatis unde omnis iste natus error sit voluptatem</div>
  <div class="card-price">$25.99</div>
  <a class="btn">Shop Now</a>
</div>

<!-- Footer -->
<footer class="abs footer">
  <div class="abs brand footer-brand"><span class="brand-dot"></span>Gilded Raven</div>

  <div class="label" style="left:316px;top:48px">CONTACT US</div>
  <div class="ico" style="left:315px;top:88px"><svg viewBox="0 0 12 12"><path d="M6 0.5a4 4 0 0 0-4 4c0 3 4 7 4 7s4-4 4-7a4 4 0 0 0-4-4z" fill="#fff"/><circle cx="6" cy="4.5" r="1.4" fill="#a8801e"/></svg></div>
  <div class="txt" style="left:349px;top:83px">Unit 4, 1207 Cypress Hollow Road,<br>Spring TX 77380.</div>
  <div class="ico" style="left:315px;top:138px"><svg viewBox="0 0 12 12"><path d="M2.5 1l2 2-1 1.5c.8 1.6 2 2.8 3.6 3.6L8.5 7l2 2-1.5 1.8C5 10.5 1.5 7 1 3z" fill="#fff"/></svg></div>
  <div class="txt" style="left:349px;top:131px">Call Us<br>+1 281 555 0194</div>
  <div class="ico" style="left:315px;top:192px"><svg viewBox="0 0 12 12"><rect x="1" y="2.5" width="10" height="7" rx="1" fill="#fff"/><path d="M1.5 3l4.5 3.5L10.5 3" fill="none" stroke="#a8801e"/></svg></div>
  <div class="txt" style="left:349px;top:186px">E mail Us<br>hello@gildedravenstudio.com</div>

  <div class="label" style="left:726px;top:48px">MENU</div>
  <div class="txt menu" style="left:726px;top:80px">HOME</div>
  <div class="txt menu" style="left:726px;top:109px">GALLERY</div>
  <div class="txt menu" style="left:726px;top:138px">INQUIRIES</div>
  <div class="txt menu" style="left:726px;top:166px">SHOP</div>

  <div class="label" style="left:964px;top:48px">FOLLOW US</div>
  <div class="ico" style="left:963px;top:85px"></div>
  <div class="txt" style="left:997px;top:81px">Like us on<br>FRIENDBOOK</div>
  <div class="ico" style="left:963px;top:134px"></div>
  <div class="txt" style="left:997px;top:130px">Follow us on<br>CHIRPER</div>
  <div class="ico" style="left:963px;top:185px"></div>
  <div class="txt" style="left:997px;top:181px">Follow us on<br>WORKLINK</div>

  <div class="footer-rule"></div>
  <div class="copyright">Copyright © 2023 All Rights Reserved</div>
</footer>

</body>
</html>
```